wealth management firm, professional group, new model

we have a logo that works but we need a card, white background using our colors...clean look

our tag line if can be used in

Steady Counsel, Lasting Ownership

```html
<!DOCTYPE html>
<html lang="en">
<head>
<meta charset="UTF-8">
<title>Larkmont Advisory Group – Business Card</title>
<link rel="stylesheet" href="https://fonts.googleapis.com/css2?family=Montserrat:wght@400;500;700&display=swap">
<style>
  :root {
    --navy: #1b2a4e;
    --paper: #fbfbfa;
    --backdrop: #d2d2d2;
  }
  * { box-sizing: border-box; margin: 0; padding: 0; }
  html, body {
    width: 1200px; height: 1050px; overflow: hidden;
    background: var(--backdrop);
    font-family: "Montserrat", sans-serif;
    color: var(--navy);
  }
  .sheet {
    width: 1200px; height: 1050px;
    display: flex; flex-direction: column; align-items: center;
    gap: 30px; padding-top: 30px;
  }
  .card {
    position: relative;
    width: 840px; height: 480px;
    background: var(--paper);
    box-shadow: 0 6px 18px rgba(0,0,0,0.12);
  }

  /* Company name */
  .company {
    display: flex; align-items: center; justify-content: center; gap: 14px;
    font-weight: 500; line-height: 1.2; white-space: nowrap;
  }
  .company__dot {
    width: 14px; height: 14px; border-radius: 50%;
    background: var(--navy); flex: none;
  }

  /* Front */
  .card--front .company {
    position: absolute; left: 0; right: 0; top: 180px;
    font-size: 40px;
  }
  .tagline-rule {
    position: absolute; left: 0; right: 0; top: 330px;
    display: flex; align-items: center; gap: 18px;
  }
  .tagline-rule::before, .tagline-rule::after {
    content: ""; flex: 1; height: 2px; background: var(--navy);
  }
  .tagline-rule__text {
    font-size: 18px; font-weight: 500; letter-spacing: 1px; white-space: nowrap;
  }

  /* Back */
  .card--back { display: flex; align-items: center; }
  .card--back .company { width: 420px; font-size: 25px; gap: 10px; }
  .card--back .company__dot { width: 11px; height: 11px; }
  .divider { width: 2px; height: 300px; background: var(--navy); }
  .contact { padding-left: 40px; }
  .contact__name { font-size: 28px; font-weight: 700; letter-spacing: 0.5px; line-height: 1; }
  .contact__role { font-size: 19px; font-weight: 500; margin-top: 6px; }
  .contact__address { font-size: 18px; font-weight: 500; line-height: 1.45; margin-top: 18px; }
  .contact__list { list-style: none; margin-top: 16px; font-size: 18px; font-weight: 500; line-height: 1.5; }
  .contact__list li { display: flex; align-items: center; gap: 8px; }
  .contact__phone { letter-spacing: 4px; }
  .icon { width: 15px; height: 15px; fill: var(--navy); flex: none; }
</style>
</head>
<body>
<main class="sheet">
  <section class="card card--front">
    <p class="company"><span class="company__dot"></span>Larkmont Advisory Group</p>
    <div class="tagline-rule">
      <span class="tagline-rule__text">Steady Counsel, Lasting Ownership</span>
    </div>
  </section>

  <section class="card card--back">
    <p class="company"><span class="company__dot"></span>Larkmont Advisory Group</p>
    <div class="divider"></div>
    <div class="contact">
      <p class="contact__name">DANIEL HARTLEY</p>
      <p class="contact__role">Advisor</p>
      <p class="contact__address">480 Lakeview Ave<br>Maitland, FL 32751</p>
      <ul class="contact__list">
        <li>
          <svg class="icon" viewBox="0 0 16 16" aria-hidden="true"><path d="M3.6 1.2l2.2 2.6-1.3 1.8c.9 2 2.4 3.5 4.4 4.4l1.8-1.3 2.6 2.2-1.2 2.4C7.4 13.6 2.4 8.6 1.2 3.1z"/></svg>
          <span class="contact__phone">407-555-0186</span>
        </li>
        <li>
          <svg class="icon" viewBox="0 0 16 16" aria-hidden="true"><path d="M1 3h14v10H1z M2.3 4.2L8 8.6l5.7-4.4z" fill-rule="evenodd"/></svg>
          <span>info@larkmontadvisory.com</span>
        </li>
        <li>
          <svg class="icon" viewBox="0 0 16 16" aria-hidden="true"><circle cx="8" cy="8" r="6.5" fill="none" stroke="#1b2a4e" stroke-width="1.4"/><ellipse cx="8" cy="8" rx="2.8" ry="6.5" fill="none" stroke="#1b2a4e" stroke-width="1.2"/><path d="M1.5 8h13" stroke="#1b2a4e" stroke-width="1.2"/></svg>
          <span>larkmontadvisory.com</span>
        </li>
      </ul>
    </div>
  </section>
</main>
</body>
</html>
```